Branding product image: VELMOT (Golden Papaya) in Plastic Cup (Ready to Eat)

The product is sliced Fruit in Light syrup
Flavour: VELMOT (Golden Papaya)
The temporary product name: VELMOT
I want the product design to be something 'fun', 'natural', and 'colourful'
The design concept could be anything depends on your imagination, but it must be eye catchy and attractive.
Basically, I want you to be creative in designing the logo and the overall graphic design for the label.
The measurement is 20 cm (Length) x 6,5 cm (Height)
The target customers are young and health conscious audiences (10 years - 65 years old).
Create something different. Something extraordinary.
Brief summary about the fruit:
This fruit only grows in certain part of the world. It grows in mountain area that is in tropical climate. The fruit flesh has a yellowish-golden color. It has an extraordinary taste (unlike normal papaya) and it suits very well with any dishes from cold appetizer, white/ red meat, desserts, and cocktails.
I need a packaging design for Fruit Cup productThe product is sliced Fruit in Light syrup.There will be various flavours i.e. apple, lychee, peach, papaya, etc.However, you may design the product using one sample flavour (i.e. papaya) first, as the designs of other flavours could be adjusted afterwards.The temporary product name is: RICCANAI want the product design to be something 'fun', 'natural', and 'colourful'.The design concept could be anything depends on your imagination. Basically, I want you to be creative in designing the logo and the overall graphic design for the label. - Create something different. Something extraordinary -Additional:The measurement is 20cm (Length) x 5cm (Height).The target customers are young audiences (10 years - 35 years old).The product design must stand out in the supermarket shelf.It must be eye catchy and attractive.Thank you,Jordan-PLEASE REFER TO DESIGN SAMPLE ATTACHED TO HAVE A BETTER UNDERSTANDING FOR THE PRODUCT CONCEPT- Added Wednesday, September 17, 2014
Project Deadline Extended Reason: Haven't found a good design. Added Friday, September 19, 2014
Project Deadline Extended Reason: Need more time for designers to finalize and perfect the design.Thank you,Jordan Added Monday, September 29, 2014
Project Deadline Extended Reason: I haven't found a great design yet. Added Tuesday, February 24, 2015
Reason: Getting better designs now. Still Open to new ideas while refining the latest designs from some designers.
Please do your best in submitting other great designs!

```html
<!DOCTYPE html>
<html lang="en">
<head>
<meta charset="utf-8">
<title>DOSUVEL Sliced in Light Syrup – Label</title>
<link rel="stylesheet" href="https://fonts.googleapis.com/css2?family=Fredoka:wght@600&family=Arimo:wght@400&display=swap">
<style>
  :root {
    --page-bg: #ffffff;
    --label-green: #8cc63f;
    --panel-cream: #fdf6c8;
    --panel-cream-deep: #f6e9a6;
    --accent-red: #d9272e;
    --accent-red-dark: #a91d22;
    --brand-green: #6aa92f;
    --ribbon-text: #fff6e0;
    --fruit-orange: #f5741f;
    --fruit-orange-light: #fbb05e;
    --ink: #1a1a1a;
  }
  html, body {
    margin: 0;
    padding: 0;
    width: 1145px;
    height: 1200px;
    overflow: hidden;
    background: var(--page-bg);
  }
  .label-canvas {
    display: block;
    width: 1145px;
    height: 1200px;
  }
  .brand-name {
    font-family: "Fredoka", "Arial Rounded MT Bold", sans-serif;
    font-weight: 600;
    font-size: 72px;
    fill: var(--brand-green);
  }
  .ribbon-text {
    font-family: "Fredoka", "Arial Rounded MT Bold", sans-serif;
    font-weight: 600;
    font-size: 20px;
    fill: var(--ribbon-text);
  }
  .net-weight {
    font-family: "Arimo", Arial, sans-serif;
    font-size: 19px;
    fill: var(--ink);
  }
</style>
</head>
<body>
<svg class="label-canvas" viewBox="0 0 1145 1200" xmlns="http://www.w3.org/2000/svg">
  <defs>
    <clipPath id="label-area">
      <rect x="50" y="430" width="1045" height="340"/>
    </clipPath>
    <radialGradient id="panel-fill" cx="0.5" cy="0.45" r="0.6">
      <stop offset="0" stop-color="#fffbe3"/>
      <stop offset="0.7" stop-color="var(--panel-cream)"/>
      <stop offset="1" stop-color="var(--panel-cream-deep)"/>
    </radialGradient>
    <linearGradient id="photo-fill" x1="0" y1="0" x2="1" y2="1">
      <stop offset="0" stop-color="var(--fruit-orange-light)"/>
      <stop offset="1" stop-color="var(--fruit-orange)"/>
    </linearGradient>
  </defs>

  <g class="label" clip-path="url(#label-area)">
    <rect class="label-band" x="50" y="430" width="1045" height="340" fill="var(--label-green)"/>
    <g class="centre-panel">
      <ellipse class="panel-swoosh" cx="572" cy="600" rx="222" ry="250" fill="var(--accent-red)" transform="rotate(18 572 600)"/>
      <ellipse class="panel-face" cx="578" cy="598" rx="200" ry="250" fill="url(#panel-fill)" transform="rotate(18 578 598)"/>
    </g>
  </g>

  <g class="brand-block">
    <text class="brand-name" x="572" y="530" text-anchor="middle">Dosuvel</text>
    <g class="ribbon">
      <path d="M432 548 L446 540 L446 574 L432 582 Z" fill="var(--accent-red-dark)"/>
      <path d="M712 548 L698 540 L698 574 L712 582 Z" fill="var(--accent-red-dark)"/>
      <path d="M446 540 Q572 556 698 540 L698 574 Q572 590 446 574 Z" fill="var(--accent-red)"/>
      <text class="ribbon-text" x="572" y="570" text-anchor="middle">Sliced in Light syrup</text>
    </g>
  </g>

  <rect class="fruit-photo" role="img" aria-label="Photo of sliced golden papaya wedges with dark seeds"
        x="462" y="600" width="214" height="112" rx="14" fill="url(#photo-fill)"/>

  <text class="net-weight" x="562" y="748" text-anchor="middle">NET WT 6 OZ (170g)</text>
</svg>
</body>
</html>
```